Design for a group involved in running bars and restaurants. They are all based in Singapore

I run a few concept bars & restaurants
1) Traditional French restaurant called Le Morvandel
2) french steakhouse chain called Les Tonnelles
3) Wine & Whisky bar called Flagon and Cask

Know more at
www.lestonnelles.sg
www.lemorvandel.sg
www.flagonandcask.com

Idea is to get people to feel that these are all part of one group although they have different brandings and logo.

Mention List of outlets (preferably on the reverse):
1) Le Morvandel
42 Verlane Street, Singapore 071286, Tel: +65.6310.4582
2) Les Tonnelles Merrow Hill
9 Merrow Hill Road, Singapore 072315, Tel: +65.6518.2946
3) Les Tonnelles Quai Vert
37 Tolbrook Quay, #02-05 Singapore, Tel: +65.6841.7390
4) Flagon and Cask
16 Merrow Hill Road, Singapore 072341, Tel: +65.6518.6172

Target Market(s)

People who generally love food, wine and whiskies based in Singapore

Industry/Entity Type

Restaurant

Contact Information for Business Card

Prefer to keep all logos

Font styles to use
Script

Requirements
Must have
• Need to keep all logos.
• Mention List of outlets:
• 1) Le Morvandel
• 42 Verlane Street, Singapore 071286, Tel: +65.6310.4582
• 2) Les Tonnelles Merrow Hill
• 9 Merrow Hill Road, Singapore 072315, Tel: +65.6518.2946
• 3) Les Tonnelles Quai Vert
• 37 Tolbrook Quay, #02-05 Singapore, Tel: +65.6841.7390
• 4) Flagon and Cask
• 16 Merrow Hill Road, Singapore 072341, Tel: +65.6518.6172
Nice to have
• Devesh Malor
• +65.9387.5146
• devesh.malor@morvandelgroup.example
Should not have
• No designation required

```html
<!DOCTYPE html>
<html lang="en">
<head>
<meta charset="utf-8">
<title>Morvandel Group Business Card</title>
<link href="https://fonts.googleapis.com/css2?family=Roboto:wght@400;700&family=Roboto+Condensed:wght@300;400;700&display=swap" rel="stylesheet">
<style>
  :root {
    --backdrop: #e9e6e2;
    --card: #ffffff;
    --ink: #111111;
    --text: #4a4a4a;
    --heading: #555555;
    --rule: #9a9a9a;
    --green: #1c7a45;
    --gold: #d2ae58;
    --black: #000000;
  }
  * { margin: 0; padding: 0; box-sizing: border-box; }
  html, body {
    width: 1125px; height: 1200px; overflow: hidden;
    background: var(--backdrop);
  }
  .card {
    position: absolute; left: 145px; width: 800px;
    background: var(--card);
    box-shadow: 0 4px 10px rgba(0,0,0,0.25);
  }
  /* Front */
  .card-front {
    top: 95px; height: 455px;
    border-bottom: 8px solid var(--black);
  }
  .holder-name {
    position: absolute; left: 48px; top: 296px;
    font: 700 29px/1 "Roboto", sans-serif; color: var(--ink);
    letter-spacing: 0.3px;
  }
  .name-rule {
    position: absolute; left: 48px; top: 342px; width: 704px;
    border-top: 1.5px solid #333;
  }
  .contact-list {
    position: absolute; left: 48px; top: 360px; list-style: none;
    font: 400 18px/24px "Roboto Condensed", sans-serif; color: var(--text);
  }
  .contact-list li { display: flex; align-items: center; gap: 11px; }
  .contact-list svg { width: 16px; flex: none; }

  /* Back */
  .card-back { top: 611px; height: 457px; }
  .outlet {
    position: absolute; display: flex; align-items: center;
  }
  .outlet-mark {
    width: 120px; display: flex; align-items: center; justify-content: center;
    font: 700 16px/1.15 "Roboto Condensed", sans-serif; text-align: center;
  }
  .mark-green { color: var(--green); }
  .mark-black { color: var(--black); }
  .mark-gold { color: var(--gold); }
  .outlet-info {
    font: 300 19px/24px "Roboto Condensed", sans-serif; color: var(--text);
  }
  .outlet-name { font-weight: 700; color: var(--heading); display: block; }
  .outlet-tel { font-weight: 400; color: #333; display: block; }
  .outlet-1 { left: 52px; top: 72px; }
  .outlet-1 .outlet-info { margin-left: 12px; }
  .outlet-2 { left: 428px; top: 69px; }
  .outlet-2 .outlet-info { margin-left: -4px; }
  .outlet-3 { left: 52px; top: 290px; }
  .outlet-3 .outlet-info { margin-left: 11px; }
  .outlet-4 { left: 436px; top: 295px; }
  .outlet-4 .outlet-info { margin-left: 33px; }

  .web-strip {
    position: absolute; left: 73px; top: 206px; width: 657px; height: 40px;
    border-top: 1.5px solid #bbb; border-bottom: 1.5px solid #bbb;
    display: flex; align-items: center; justify-content: center; gap: 14px;
    font: 400 19px/1 "Roboto", sans-serif; color: var(--text);
  }
  .web-green { color: var(--green); }
  .web-gold { color: var(--gold); }
  .web-sep { color: #777; }
</style>
</head>
<body>

<section class="card card-front">
  <h1 class="holder-name">DEVESH MALOR</h1>
  <div class="name-rule"></div>
  <ul class="contact-list">
    <li>
      <svg viewBox="0 0 16 22" aria-hidden="true"><rect x="2" y="1" width="12" height="20" rx="2" fill="none" stroke="#111" stroke-width="2"/><rect x="4" y="4" width="8" height="12" fill="#111"/></svg>
      +65.9387.5146
    </li>
    <li>
      <svg viewBox="0 0 16 12" aria-hidden="true"><rect x="0" y="1" width="16" height="10" fill="#111"/><path d="M0 1 L8 7 L16 1" fill="none" stroke="#fff" stroke-width="1.4"/></svg>
      devesh.malor@morvandelgroup.example
    </li>
  </ul>
</section>

<section class="card card-back">
  <div class="outlet outlet-1">
    <div class="outlet-mark mark-green">Le Morvandel</div>
    <p class="outlet-info"><span class="outlet-name">Le Morvandel</span>42 Verlane Street<br>Singapore 071286<span class="outlet-tel">Tel: +65.6310.4582</span></p>
  </div>
  <div class="outlet outlet-2">
    <div class="outlet-mark mark-black">Les Tonnelles</div>
    <p class="outlet-info"><span class="outlet-name">Les Tonnelles Quai Vert</span>37 Tolbrook Quay<br>#02-05 Singapore<span class="outlet-tel">Tel: +65.6841.7390</span></p>
  </div>

  <div class="web-strip">
    <span class="web-green">www.lemorvandel.sg</span>
    <span class="web-sep">|</span>
    <span>www.lestonnelles.sg</span>
    <span class="web-sep">|</span>
    <span class="web-gold">www.flagonandcask.com</span>
  </div>

  <div class="outlet outlet-3">
    <div class="outlet-mark mark-black">Les Tonnelles</div>
    <p class="outlet-info"><span class="outlet-name">Les Tonnelles Merrow Hill</span>9 Merrow Hill Road<br>Singapore 072315<span class="outlet-tel">Tel: +65.6518.2946</span></p>
  </div>
  <div class="outlet outlet-4">
    <div class="outlet-mark mark-gold">Flagon and Cask</div>
    <p class="outlet-info"><span class="outlet-name">Flagon and Cask</span>16 Merrow Hill Road<br>Singapore 072341<span class="outlet-tel">Tel: +65.6518.6172</span></p>
  </div>
</section>

</body>
</html>
```